Brell Stone Company Business Cards

Front and Back Business Card - logo and text setup - cool design. I need workable photoshop or illustrator files so I can setup each employee card with design that is created
Updates

Hi everyone, thank you for the great entries. Please no more white and blue cards - there are so many already - black and silver only now please. thanks!

Target Market(s)

Construction Industry - Facility Managers

Industry/Entity Type

Construction

Contact Information for Business Card

I really like contemporary simplistic looks - clean neat....not opposed to seeing some black backrounds

Requirements
Must have
• Logo/website address with design on front only - www.brellstone-example.com (logo attached)
• Back:
• Name/Title/Company Address/Phone/email address
Nice to have
• Cool design
Should not have
• Nothing gimmicky like Fire or Water - since we are a Fire Protection company - it has all been done

```html
<!DOCTYPE html>
<html lang="en">
<head>
<meta charset="utf-8">
<title>Brell Stone Company Business Cards</title>
<link rel="stylesheet" href="https://fonts.googleapis.com/css2?family=Open+Sans:wght@400;600;700;800&display=swap">
<style>
  :root {
    --page-bg: #1a1a1b;
    --card-bg: #2a2a2c;
    --silver: #c9cbcf;
    --silver-dark: #9a9da2;
    --text-light: #e6e7e9;
    --divider: #7d7f84;
  }
  * { margin: 0; padding: 0; box-sizing: border-box; }
  html, body {
    width: 1200px; height: 874px; overflow: hidden;
    background: var(--page-bg);
    font-family: "Open Sans", Arial, sans-serif;
  }
  .sheet {
    position: relative; width: 1200px; height: 874px;
    display: flex; flex-direction: column; align-items: center; justify-content: center;
    gap: 28px;
  }
  .card {
    position: relative; width: 700px; height: 400px;
    background: var(--card-bg); border-radius: 20px;
    box-shadow: 0 10px 30px rgba(0,0,0,0.45);
  }
  .card-front {
    display: flex; flex-direction: column; align-items: center; justify-content: center;
    gap: 18px;
  }
  .brand-name {
    font-weight: 800; font-size: 78px; letter-spacing: -1px;
    color: var(--silver); line-height: 1;
  }
  .front-web {
    font-weight: 400; font-size: 19px; letter-spacing: 1px;
    color: var(--silver-dark);
  }
  .identity {
    position: absolute; right: 392px; top: 158px; text-align: right;
  }
  .person-name { font-weight: 700; font-size: 30px; color: var(--silver); line-height: 1.1; }
  .person-title { font-weight: 400; font-size: 19px; color: var(--silver-dark); margin-top: 2px; }
  .divider {
    position: absolute; left: 330px; top: 138px; width: 1px; height: 112px;
    background: var(--divider);
  }
  .contact-list {
    position: absolute; left: 352px; top: 140px; list-style: none;
  }
  .contact-list li {
    display: flex; align-items: center; gap: 10px;
    font-size: 17px; color: var(--text-light); height: 27px;
  }
  .icon { width: 16px; height: 16px; flex: none; }
  .address {
    position: absolute; left: 42px; bottom: 48px;
    display: flex; align-items: center; gap: 10px;
    font-size: 17px; color: var(--text-light);
  }
</style>
</head>
<body>
<main class="sheet">
  <section class="card card-front" aria-label="Card front">
    <span class="brand-name">Brell Stone</span>
    <span class="front-web">www.brellstone-example.com</span>
  </section>

  <section class="card card-back" aria-label="Card back">
    <div class="identity">
      <p class="person-name">Daniel Reyes</p>
      <p class="person-title">CEO/Founder</p>
    </div>
    <div class="divider"></div>
    <ul class="contact-list">
      <li>
        <svg class="icon" viewBox="0 0 16 16"><path fill="#c9cbcf" d="M3.2 1.5l2.3-.5 1.4 3.3-1.5 1.1c.7 1.6 1.9 2.9 3.5 3.7l1.2-1.4 3.3 1.5-.5 2.3c-.2.8-1 1.3-1.8 1.2C5.8 12.2 2.3 8.5 1.8 3.3c-.1-.8.5-1.6 1.4-1.8z"/></svg>
        (555) 014-2278
      </li>
      <li>
        <svg class="icon" viewBox="0 0 16 16"><rect x="4" y="1.5" width="8" height="4" fill="#c9cbcf"/><rect x="1" y="6" width="14" height="6" rx="1" fill="#c9cbcf"/><rect x="4" y="10" width="8" height="4.5" fill="#2a2a2c" stroke="#c9cbcf" stroke-width="1"/></svg>
        (555) 014-2279
      </li>
      <li>
        <svg class="icon" viewBox="0 0 16 16"><rect x="1" y="3" width="14" height="10" rx="1" fill="#c9cbcf"/><path d="M1.5 3.8L8 9l6.5-5.2" stroke="#2a2a2c" stroke-width="1.3" fill="none"/></svg>
        info@brellstone-example.com
      </li>
      <li>
        <svg class="icon" viewBox="0 0 16 16"><circle cx="8" cy="8" r="6.5" fill="none" stroke="#c9cbcf" stroke-width="1.6"/><ellipse cx="8" cy="8" rx="2.8" ry="6.5" fill="none" stroke="#c9cbcf" stroke-width="1.2"/><path d="M1.5 8h13" stroke="#c9cbcf" stroke-width="1.2"/></svg>
        www.brellstone-example.com
      </li>
    </ul>
    <p class="address">
      <svg class="icon" viewBox="0 0 16 16"><path fill="#c9cbcf" d="M8 .8a5 5 0 0 0-5 5c0 3.7 5 9.4 5 9.4s5-5.7 5-9.4a5 5 0 0 0-5-5zm0 7a2 2 0 1 1 0-4 2 2 0 0 1 0 4z"/></svg>
      48 Quarry Lane, Northfield, NY 10001
    </p>
  </section>
</main>
</body>
</html>
```